Nutritional & Gastrointestinal Health Consulting Service-Website design

We need a website design for a new health consulting service called "Bright Vale" based in Perth, Australia.

We will be providing consulting services in the areas of:
1) Nutrition and Diet
2) Gastrointestinal Health (which means stomach & digestive system related health)

These consulting services will be provided by an Accredited Dietitian and a Paediatric Gastroenterologist.

We are open to creative ideas in terms of design, layout, fonts and colours. We also would love to see images of nature in the backdrop with families (adults with kids) having a good time, fresh fruits and vegetables displayed in a farmer's market or supermarket. 2 or 3 images should be sufficient. We would also definitely want our logo somewhere in the main page of website. The logo file is also attached. Please have a look at a website's design that we really liked. We would love to see designs inspired by that style. The website details are in the in the "nice to have priorities" section of this project brief.

We also would be looking at website designers with software coding skills so that if we like the design we can go ahead with the next step of coding.

The website design should communicate the purpose of the website and at the same time be simple, elegant and unique/eye-catching.

We look forward to receiving creative ideas for our website from you all. Good luck!

More details have been added to our project- for example: Logo, fonts style, must haves etc etc. Please view the updated project brief. Looking forward to receiving your fantastic ideas for our website. Thanking you

Hi, I have updated the colour preference. Will add the content preferences tomorrow. thanks

Hello all, I have now added a LOT more content to what we want in our website. It is very much in detail, so please carefully have a read through the entire project brief. If you have any questions write back to me and I will try to respond as quickly as I can. Last few days were busy so couldn't respond quickly to all of you who had send me designs/queries/questions. Thank you for your patience. I look forward to receiving fantastic designs from you all. Good Luck :-)

Target Market(s)

Adults based in western speaking countries aged 18 to 60 years

Industry/Entity Type

Software

Font styles to use
Sans Serif
Script

Colors
faa54b
acd036

Requirements
Must have
• The website must have the MAIN logo file attached. I have attached 3 files: 1) MAIN logo; 2) supplementary logo A ; 3) supplementary logo B

I have selected 2 colours from the colour scheme (see below)-(as the colour of our logo is that).
However we would also like to see LIGHT CHOCOLATE BROWN or CHOCOLATE BROWN colour used as the background colour of the website
Preferred WEBSITE CONTENT:
1) HOME PAGE:
Content required=
--Company Logo
--Dr Dorian Pelham
Paediatric Gastroenterologist & Hepatologist
-Marla Pelham.
Dietitian & Nutritionist
--Website Menu (either listed horizontally or vertically):
Once clicked on each name:

Under each of the Website Menu items we want the following Headings to be added

2) ABOUT US page:
Sub-heading under this: Qualification, Skills, Special Interest

3) SERVICES
DORIAN'S PAGE: Individual Consultation, Endoscopy procedures
Individual Consultation, Group Based Services, Food Diary, Food & Symptom Diary

4) FEES & REBATE: Content as below:
Please Note: Payment of full fees is required at the time of consultation and procedures. 48 hours notice is required for cancellation of appointments/non-attendance. Failure to provide this may result in a fee being incurred. Please call reception to find out the amount of fee charged for cancellation of appointments/non-attendance.
headings are:
Paediatric Gastroenterology:
Dorian's pge
Individual Consultation - Initial (upto 30 mins):
Review Consultation (upto 15 mins):
Endoscopy procedures - No Gap fees charged. Fees will be billed directly to Vitacover. If any queries, please contact reception.

marla's pge
sub heading:
Individual Consultation - Initial (upto 45 mins):
Individual Consultation - Review (upto 30 mins):

Concession-Individual Consultation -Initial (upto 45 mins):
Concession-Individual Consultation - Review (upto 30 mins):
Please Note: Concession applies for health care card holders & pensioners

Group Based Services: Pricing subject to the type of service provided. Please contact us for an obligation free quote.
Education Topics Include:
- Paediatric Nutrition (Introducing Solids, Fussy Eating, Healthy Eating)
- Pregnancy Nutrition, Gestational Diabetes, Breastfeeding/Lactation Nutrition
- Healthy Eating, Supermarket Shopping Tips, Nutrition Label Reading Tips, Healthier
sub heading under nutrition & diet:
-Vitacover:
--A rebate of $52.95 is available from Vitacover if an EPC ( Enhanced Primary Care)/Chronic Disease Management (CDM) plan is issued by your GP.
--All mandatory paperwork needs to be available at the time of making your appointment for your eligibility.
-Private Health Fund:
--Most private health funds provide rebate on dietetic appointments. However the rebate amount depends on your level of cover. Thus, please contact your health fund to determine your entitled rebate.
-RSB: Approved provider for RSB services

6) FOR DOCTORS: Bright Vale Paediatric Gastroenterologist Referral Form
Bright Vale Dietitian Referral form
7) LOCATIONS & CONTACT

Paediatric Gastroenterology & Hepatology Service
Suite 46
Holy Lantern Bramcote Medical Centre
17 Colin Ferris Pde,
MURDOCH, WA 6150
P: (08) 9422 5061
F: (08) 9422 3094

Nutrition & Diet Service
Suite 46
17 Colin Ferris Pde,
MURDOCH, WA 6150
P: (08) 9422 5061
F: (08) 9422 3094

Tolland Medical Centre
58-60 Karrigan Parkway,
MANDURAH, WA 6210
P: (08) 9647 2283
F: (08) 96724419
www.tmcexample.com.au

This page should have a webform that has following titles:
-Your Name
-Your Email
-Your Phone
-Message

8) NEWS & BLOG
Nice to have
• We liked the design style of the websites below:
https://www.vendoraplex.example/

http://qoravelt.example/

But feel free to use your creativity too
Should not have
• Please do not use any body building or muscle building images

```html
<!DOCTYPE html>
<html lang="en">
<head>
<meta charset="utf-8">
<title>Bright Vale – Blogs</title>
<link rel="stylesheet" href="https://fonts.googleapis.com/css2?family=Arimo:wght@400;700&display=swap">
<style>
  :root {
    --page-brown: #5b3519;
    --shell-tint: #b6a291;
    --panel-brown: #7f5d45;
    --content-tint: #dcd0c7;
    --frame-white: #f4f1ee;
    --heading-brown: #5a3016;
    --link-brown: #6b4a2e;
    --menu-orange: #f8a33a;
    --logo-green: #acd036;
    --link-yellow: #e6ec55;
    --rule-grey: #b9b3ae;
    --ink: #111111;
  }
  * { box-sizing: border-box; margin: 0; padding: 0; }
  html, body {
    width: 1200px; height: 815px; overflow: hidden;
    font-family: "Arimo", Arial, sans-serif;
    background: var(--page-brown);
  }
  .page-backdrop {
    position: absolute; inset: 0;
    background: radial-gradient(circle at 50% 45%, #6a4124 0%, var(--page-brown) 75%);
  }
  .site-shell {
    position: absolute; left: 35px; top: 37px; width: 1130px; height: 740px;
    background: var(--shell-tint);
    border: 3px solid var(--frame-white); border-radius: 14px;
    box-shadow: 0 0 3px rgba(0,0,0,.35);
  }
  .account-links {
    position: absolute; right: 40px; top: 7px;
    font-size: 13px; color: var(--link-brown);
  }
  .account-links a { color: var(--link-brown); }
  .account-links .divider { margin: 0 7px; color: #e8e0d8; }
  .site-header {
    position: absolute; left: 212px; top: 22px; width: 698px; height: 177px;
    background: var(--panel-brown);
    border: 3px solid var(--frame-white); border-radius: 14px;
    display: flex; align-items: center; justify-content: center; gap: 14px;
  }
  .brand-dot { width: 38px; height: 38px; border-radius: 50%; background: var(--menu-orange); }
  .brand-name { font-size: 40px; font-weight: 700; color: var(--logo-green); letter-spacing: 1px; }
  .box {
    position: absolute; border: 3px solid var(--frame-white); border-radius: 6px;
    box-shadow: 0 0 2px rgba(0,0,0,.3);
  }
  .side-box { background: var(--panel-brown); }
  .box-title {
    height: 29px; line-height: 26px; text-align: center;
    color: #fff; font-size: 14px; font-weight: 700;
    border-bottom: 3px solid #d7cec6;
  }
  .main-menu { left: 24px; top: 218px; width: 223px; height: 242px; }
  .main-menu ul { margin: 21px 0 0 56px; font-size: 13px; font-weight: 700; line-height: 17.6px; }
  .main-menu li { list-style: circle; color: #222; }
  .main-menu a { color: var(--menu-orange); }
  .content-area {
    left: 258px; top: 218px; width: 608px; height: 457px;
    background: var(--content-tint);
  }
  .breadcrumb {
    margin: 5px 9px 0; padding: 0 0 0 11px; height: 21px;
    border-bottom: 3px solid var(--rule-grey);
    font-size: 12px; font-weight: 700;
  }
  .breadcrumb a { color: var(--ink); }
  .page-title { margin: 12px 0 0 11px; font-size: 20px; color: var(--heading-brown); }
  .blog-post { margin: 0 22px 0 24px; border-bottom: 3px solid var(--rule-grey); }
  .post-title { font-size: 18px; margin-top: 24px; }
  .post-title a { color: var(--heading-brown); }
  .post-body { font-size: 12.6px; line-height: 15.2px; color: var(--ink); margin-top: 17px; }
  .post-author { display: block; font-size: 13px; color: var(--link-brown); margin: 18px 0 13px 6px; }
  .blog-post.older .post-title { margin-top: 14px; }
  .blog-post.older .post-author { margin-top: 3px; margin-bottom: 12px; }
  .user-login { left: 877px; top: 218px; width: 223px; height: 212px; }
  .login-form { padding: 18px 0 0 14px; color: #fff; font-size: 13px; font-weight: 700; }
  .login-form label { display: block; margin-bottom: 1px; }
  .login-form .req { color: #d33; }
  .login-form input[type=text], .login-form input[type=password] {
    width: 108px; height: 20px; border: 1px solid #888; background: #fff;
    font-family: inherit; font-size: 13px; padding: 0 2px; margin-bottom: 13px;
  }
  .login-form ul { margin: -6px 0 0 22px; font-weight: 400; }
  .login-form li { list-style: disc; color: #fff; }
  .login-form li a { color: var(--link-yellow); }
  .login-form button {
    margin-top: 12px; padding: 1px 8px; font-family: inherit; font-size: 12px;
    background: linear-gradient(#fafafa, #ddd); border: 1px solid #999; border-radius: 2px;
  }
  .site-footer {
    position: absolute; left: 0; right: 0; top: 700px; text-align: center;
    font-size: 12px; font-weight: 700; color: var(--ink);
  }
  .site-footer a { color: var(--ink); }
</style>
</head>
<body>
  <div class="page-backdrop" role="img" aria-label="Chocolate brown background with a faint pattern of hand-drawn fruits and vegetables"></div>
  <div class="site-shell">
    <nav class="account-links"><a href="#">Login</a><span class="divider">|</span><a href="#">Register</a></nav>

    <header class="site-header">
      <span class="brand-dot"></span>
      <span class="brand-name">Bright Vale</span>
    </header>

    <aside class="box side-box main-menu">
      <h2 class="box-title">Main menu</h2>
      <ul>
        <li><a href="#">Home</a></li>
        <li><a href="#">About Us</a></li>
        <li><a href="#">Nutrition &amp; Diet</a></li>
        <li><a href="#">Paediatric Gastroenterology</a></li>
        <li><a href="#">Fees &amp; Rebate</a></li>
        <li><a href="#">For Doctors</a></li>
        <li><a href="#">Location</a></li>
        <li><a href="#">Contact</a></li>
        <li><a href="#">News &amp; Blog</a></li>
      </ul>
    </aside>

    <main class="box content-area">
      <div class="breadcrumb"><a href="#">Home</a></div>
      <h1 class="page-title">Blogs</h1>
      <article class="blog-post">
        <h2 class="post-title"><a href="#">New Blog Post</a></h2>
        <p class="post-body">Quisque hendrerit nunc sit amet dui scelerisque efficitur. Morbi vitae tincidunt magna. Proin imperdiet orci non nibh mattis efficitur. Aenean ac dapibus sapien. Cras sed placerat diam, ut sollicitudin justo. In at odio nec dui suscipit eleifend. Praesent turpis diam, iaculis ut dolor tristique, vestibulum tincidunt metus. Maecenas blandit dolor eget auctor sagittis.</p>
        <a class="post-author" href="#">Tamsin's blog</a>
      </article>
      <article class="blog-post older">
        <h2 class="post-title"><a href="#">Old Blog Post</a></h2>
        <p class="post-body">Nullam consectetur, elit a venenatis posuere, metus velit tempus ante, vitae sollicitudin dolor lorem at lectus. Vivamus mollis tincidunt ex cursus commodo. Curabitur vestibulum sit amet tellus a rhoncus. Aliquam vitae urna ut libero faucibus gravida. Integer porta est quis accumsan rhoncus. Mauris vel consequat nulla. Morbi porttitor accumsan ultrices. Nam tempor at diam ut ullamcorper. Praesent cursus justo vitae lectus mollis, a molestie velit tristique. Maecenas congue feugiat lobortis. Nam vel quam ut metus fermentum commodo et vel eros. Curabitur tincidunt semper ultrices.</p>
        <a class="post-author" href="#">Tamsin's blog</a>
      </article>
    </main>

    <aside class="box side-box user-login">
      <h2 class="box-title">User login</h2>
      <form class="login-form">
        <label for="username">Username <span class="req">*</span></label>
        <input id="username" type="text" value="Tamsin">
        <label for="password">Password <span class="req">*</span></label>
        <input id="password" type="password" value="secretword1">
        <ul><li><a href="#">Request new password</a></li></ul>
        <button type="button">Log in</button>
      </form>
    </aside>

    <footer class="site-footer"><a href="#">Bright Vale</a> © Copyright 2014</footer>
  </div>
</body>
</html>
```